real esate business card with company logo and name

we need a business card design for a real esate company

The company name is Walsh & Brand Pty Ltd, and we have our logo designed and will upload. We want classic or moden feel. Black or white background. looks more textured. Should include folowinginformations
Owen Walsh and Lucy Brand
Sales Agents & Onsite Manager
p: 07 5948 2063
F: 07 5948 2174
M:0431 857 219
3/42 Marlow Crescent, FERNLEA QLD 4213

We want this business card looks professonal. Thank you in advance.

Industry/Entity Type

Real Estate Agent

Contact Information for Business Card

Owen Walsh and Lucy Brand
Onsite Manager & Sales Agents
p: 07 5948 2063
M:0431 857 219

Font styles to use
Serif

Colors
000000
fbfbfb
333333
959595

Requirements
Must have
• company logo and name, black or white back ground

```html
<!DOCTYPE html>
<html lang="en">
<head>
<meta charset="utf-8">
<title>Walsh &amp; Brand Pty Ltd – Business Card</title>
<link rel="stylesheet" href="https://fonts.googleapis.com/css2?family=Roboto+Condensed:wght@300;400&family=Montserrat:wght@600&display=swap">
<style>
  :root {
    --page: #e9e7e4;
    --frost-light: #fbfbfb;
    --frost-mid: #e6e2df;
    --frost-warm: #eadcd8;
    --panel-top: #2a2a2a;
    --panel-bottom: #050505;
    --edge: #d9d9d9;
    --ink-dark: #333333;
    --ink-grey: #959595;
    --ink-light: #e4e4e4;
    --ink-white: #fbfbfb;
    --accent-gold: #c9a878;
  }
  * { margin: 0; padding: 0; box-sizing: border-box; }
  html, body { width: 1200px; height: 969px; overflow: hidden; background: var(--page); }
  .canvas { position: relative; width: 1200px; height: 969px; }

  .card {
    position: absolute; left: 100px; top: 200px;
    width: 1000px; height: 568px;
    background: linear-gradient(160deg, var(--frost-light) 0%, var(--frost-mid) 45%, var(--frost-warm) 75%, var(--frost-mid) 100%);
    box-shadow: 0 12px 40px rgba(0,0,0,0.18);
    overflow: hidden;
    font-family: "Roboto Condensed", sans-serif;
  }
  .card-shapes { position: absolute; inset: 0; }

  .brand { position: absolute; left: 60px; top: 150px; width: 340px; text-align: center; }
  .brand-square { width: 120px; height: 120px; margin: 0 auto 52px; background: var(--ink-grey); }
  .brand-name {
    font-family: "Montserrat", sans-serif; font-weight: 600;
    font-size: 27px; letter-spacing: 1px; color: var(--ink-dark); white-space: nowrap;
  }

  .details { position: absolute; right: 54px; top: 160px; text-align: right; }
  .agents { font-size: 32px; font-weight: 400; color: var(--ink-light); line-height: 1; }
  .agents .second { color: var(--ink-white); }
  .role { margin-top: 12px; font-size: 23px; font-weight: 400; color: var(--accent-gold); }

  .contacts { list-style: none; margin-top: 20px; padding-right: 0; }
  .contacts li {
    display: flex; justify-content: flex-end; align-items: center; gap: 14px;
    font-size: 22px; font-weight: 300; color: var(--ink-light); height: 38px; margin-right: -8px;
  }
  .contacts svg { width: 26px; height: 26px; fill: none; stroke: var(--ink-light); stroke-width: 1.8; }

  .address { margin-top: 14px; font-size: 22px; font-weight: 300; line-height: 32px; color: var(--ink-grey); }
  .address .locality { color: var(--accent-gold); }
</style>
</head>
<body>
<main class="canvas">
  <section class="card" aria-label="Business card">
    <svg class="card-shapes" viewBox="0 0 1000 568" preserveAspectRatio="none" aria-hidden="true">
      <defs>
        <linearGradient id="panelFill" x1="0" y1="0" x2="0" y2="1">
          <stop offset="0" stop-color="var(--panel-top)"/>
          <stop offset="1" stop-color="var(--panel-bottom)"/>
        </linearGradient>
      </defs>
      <polygon points="392,0 1000,0 1000,568 382,568 582,284" fill="url(#panelFill)"/>
      <polyline points="372,0 560,284 364,568" fill="none" stroke="var(--edge)" stroke-width="3"/>
      <polyline points="392,0 582,284 382,568" fill="none" stroke="var(--ink-grey)" stroke-width="1.5"/>
    </svg>

    <div class="brand">
      <div class="brand-square"></div>
      <p class="brand-name">WALSH &amp; BRAND PTY LTD.</p>
    </div>

    <div class="details">
      <h1 class="agents">Owen Walsh &amp; <span class="second">Lucy Brand</span></h1>
      <p class="role">Sales Agents &amp; Onsite Manager</p>
      <ul class="contacts">
        <li>07 5948 2063
          <svg viewBox="0 0 24 24" aria-label="Phone"><path d="M6 3l3 0 2 5-2 1.5c1 2.5 3 4.5 5.5 5.5L16 13l5 2v3c0 1-1 2-2 2C10 20 4 14 4 5c0-1 1-2 2-2z"/></svg>
        </li>
        <li>0431 857 219
          <svg viewBox="0 0 24 24" aria-label="Mobile"><rect x="6" y="2" width="12" height="20" rx="2"/><line x1="6" y1="18" x2="18" y2="18"/></svg>
        </li>
        <li>07 5948 2174
          <svg viewBox="0 0 24 24" aria-label="Fax"><rect x="3" y="10" width="18" height="9" rx="1"/><rect x="7" y="4" width="10" height="6"/><line x1="7" y1="14" x2="17" y2="14"/></svg>
        </li>
      </ul>
      <address class="address" style="font-style:normal">
        3/42 Marlow Crescent<br>
        <span class="locality">FERNLEA QLD 4213</span>
      </address>
    </div>
  </section>
</main>
</body>
</html>
```